Business Card for Professional Photographer

I'm looking for an eye catching modern clean design that compliments my logo/ website fonts & colours.
I specialise in architecture, corporate & commercial photography so I'm marketing to professional clients rather than portrait / wedding clients.

I would prefer to not have a solid black design.

My logo brand guide is as follows :

Main front font. : Reislust
Main font colour : #fff
Slogan front font : Ubuntu Bold
Monogram front font : Venti Medium
Container colour : #fff

I need print ready files in pdf .png & .eps formats.

Included in the files below are some screen grabs as reference to font & colours etc.

```html
<!DOCTYPE html>
<html lang="en">
<head>
<meta charset="utf-8">
<title>Clearline Studio – Business Card</title>
<link href="https://fonts.googleapis.com/css2?family=Ubuntu:wght@300;400;500&display=swap" rel="stylesheet">
<style>
  :root {
    --gold: #cc9c5c;
    --white: #ffffff;
    --ink: #333333;
    --backdrop: #e4e4e4;
  }
  html, body {
    margin: 0;
    padding: 0;
    width: 1200px;
    height: 1200px;
    overflow: hidden;
    background: var(--backdrop);
  }
  .canvas {
    position: relative;
    width: 1200px;
    height: 1200px;
    font-family: "Ubuntu", sans-serif;
  }
  .card {
    position: absolute;
    left: 396px;
    width: 417px;
    height: 352px;
  }
  .card svg {
    position: absolute;
    inset: 0;
    display: block;
  }
  .card--front { top: 184px; }
  .card--back  { top: 673px; }

  .front-content {
    position: absolute;
    inset: 0;
    padding-top: 100px;
    text-align: center;
    color: var(--ink);
  }
  .holder-name {
    margin: 0;
    font-size: 23px;
    font-weight: 500;
    color: var(--gold);
    letter-spacing: 0.3px;
    line-height: 1;
  }
  .holder-title {
    margin: 6px 0 0;
    font-size: 15px;
    font-weight: 400;
    letter-spacing: 0.5px;
    line-height: 1;
  }
  .divider {
    width: 58px;
    height: 0;
    border: 0;
    border-top: 1.5px solid var(--ink);
    margin: 12px auto 11px;
  }
  .contact-block {
    margin: 0;
    font-size: 15.5px;
    font-weight: 400;
    line-height: 19px;
  }

  .brand {
    position: absolute;
    left: 60px;
    top: 160px;
    display: flex;
    align-items: center;
    gap: 16px;
  }
  .brand-mark {
    width: 26px;
    height: 26px;
    border: 2px solid var(--white);
    box-sizing: border-box;
  }
  .brand-name {
    font-size: 22px;
    font-weight: 300;
    color: var(--white);
    letter-spacing: 3px;
    text-transform: uppercase;
    line-height: 1;
  }
</style>
</head>
<body>
<main class="canvas">

  <section class="card card--front">
    <svg width="417" height="352" viewBox="0 0 417 352" aria-hidden="true">
      <defs>
        <clipPath id="card-shape-front">
          <path d="M0,90 Q0,50 40,50 H80 Q92,50 92,38 V35 Q92,0 127,0 H289 Q324,0 324,35 V38 Q324,50 336,50 H377 Q417,50 417,90 V312 Q417,352 377,352 H40 Q0,352 0,312 Z"/>
        </clipPath>
      </defs>
      <path clip-path="url(#card-shape-front)" fill="#ffffff" stroke="#cc9c5c" stroke-width="36"
            d="M0,90 Q0,50 40,50 H80 Q92,50 92,38 V35 Q92,0 127,0 H289 Q324,0 324,35 V38 Q324,50 336,50 H377 Q417,50 417,90 V312 Q417,352 377,352 H40 Q0,352 0,312 Z"/>
    </svg>
    <div class="front-content">
      <h1 class="holder-name">LENA HARTWELL</h1>
      <p class="holder-title">PRESIDENT</p>
      <hr class="divider">
      <p class="contact-block">214 Birchwood Avenue<br>Juneau, Alaska 99801</p>
      <hr class="divider">
      <p class="contact-block">P. 907-555-0148<br>info@clearlinestudio.com<br>clearlinestudio.com</p>
    </div>
  </section>

  <section class="card card--back">
    <svg width="417" height="352" viewBox="0 0 417 352" aria-hidden="true">
      <path fill="#cc9c5c"
            d="M0,90 Q0,50 40,50 H80 Q92,50 92,38 V35 Q92,0 127,0 H289 Q324,0 324,35 V38 Q324,50 336,50 H377 Q417,50 417,90 V312 Q417,352 377,352 H40 Q0,352 0,312 Z"/>
    </svg>
    <div class="brand">
      <span class="brand-mark"></span>
      <span class="brand-name">Clearline Studio</span>
    </div>
  </section>

</main>
</body>
</html>
```